Elegant, Playful ReDesign of Paperlynx Website in wordpress - Budget has been raised

Project Brief: Paperlynx Website Redesign in WordPress

Introduction: Paperlynx, a cutting-edge document creation solution, aims to revolutionize the tedious process of crafting contracts, offers, forms, and other documents. By saving customers valuable time, streamlining workflows, and minimizing human error, Paperlynx has become an essential tool. As a technology company with a diverse clientele, we're set to boost our online presence through a refreshed WordPress website. Beyond a modernized website, we aspire to establish a stronger brand identity, incorporating graphic elements seamlessly into our online presence.

Current Status: Currently hosted on WordPress, Paperlynx's existing website serves its purpose but is ready for a visual transformation. Our goal is to maintain a modern and attractive appearance while upholding our commitment to simplicity and efficiency. Notably, the website is currently only in Danish. The redesigned structure should include a language switch function to cater to future international customers.

Objectives:
• Modern Aesthetic: Redesign the website with a fresh and modern vibe, reflecting innovation in the document creation sphere.
• User-Friendly: Prioritize an intuitive design for seamless navigation, ensuring visitors easily understand our offerings and benefits.
• Informative Content: Strike a balance between attractiveness and informativeness, clearly communicating Paperlynx's value proposition and simplifying business processes.
• Graphic Elements: Integrate visually appealing graphics that enhance the site's aesthetics and contribute to our overall visual identity. These elements should be versatile for future use in social media, advertisements, and other branding materials.
• Brand Recognition: Maintain our current logo and color scheme while exploring creative ways to establish a distinctive brand identity. The website should be a cornerstone for a cohesive branding strategy.
• Media Integration: Include images or videos on the website to enhance engagement. Find suitable, free-to-use visuals.
• Responsiveness: Ensure the design is responsive and works seamlessly on all devices.
• Demo Booking Form: Improve the design of the form to book a demo.
• Multilingual Support: Enable language transformation; the website is currently in Danish but should cater to other countries.

Guidelines:
• Typography: Up to the designer's discretion.
• Images/Videos: Must be free to use without additional charges.
• WordPress Theme: Use any WordPress theme below $100.
• Logo Redesign: Not needed; stick to the referenced color palette, as our new logo uses these colors.
• Color Palette: Stick to the existing company colors for consistency:
RGB
• #000b3c
• #004c6c
• #319ac3
• Greytones and white are also allowed
• Creativity Encouraged: Embrace creativity within the color palette for the layout, visuals, and overall user experience.

Conclusion: The Paperlynx website redesign marks an exciting opportunity to enhance our online presence. Our goal is to achieve a balance between a modern, attractive design and a clear, informative representation of our innovative solutions. We envision the revamped website as the foundation for a compelling online brand presence, with versatile graphic elements resonating across various digital platforms.

Sections that the website must include: Space for customer logos, space for testimonials, Space and redesign for display of price structure and price comparison, sections for company details and other information.

Design should also include a redesign of the customer cases section.
Generally there should just be a redesign of all things that are on the website.

Link to current website: https://paperlynx.example/

Target Market(s)

+50 employees.

Industry/Entity Type

Document automation

Coding

Coded - Design and coding required

Number of Pages Required

5+ page

Colors
0054AA
0677BA
7BADD7
CADEEF
E8F1F8

Requirements
Must have
• The new webpage must have the same pages as the current one. Frontpage, Book demo, About us, Case stories and Pricing

```html
<!DOCTYPE html>
<html lang="en">
<head>
<meta charset="utf-8">
<title>Paperlynx – Prices</title>
<link rel="stylesheet" href="https://fonts.googleapis.com/css2?family=Barlow+Condensed:wght@500;600;700&family=Roboto:wght@400;500;700&family=Raleway:wght@400;600&display=swap">
<style>
  :root {
    --navy: #000b3c;
    --deep: #23658a;
    --deep-dark: #004c6c;
    --sky: #47a4da;
    --sky-brand: #319ac3;
    --ink: #1c1c1c;
    --muted: #a9a9a9;
    --row-alt: #ebebeb;
    --toggle-off: #c9c9c9;
    --band: #cfe2ea;
    --white: #ffffff;
  }
  * { box-sizing: border-box; margin: 0; padding: 0; }
  html, body { width: 1200px; height: 722px; overflow: hidden; background: var(--white); }
  body { font-family: "Roboto", sans-serif; color: var(--ink); position: relative; }

  .site-header {
    height: 48px; display: flex; align-items: center; justify-content: space-between;
    padding: 0 70px; border-bottom: 1px solid #f0f0f0;
  }
  .brand { display: flex; align-items: center; gap: 8px; text-decoration: none; }
  .brand-mark { width: 16px; height: 16px; background: var(--sky-brand); }
  .brand-name { font-weight: 700; font-size: 17px; color: var(--deep-dark); letter-spacing: .5px; }
  .main-nav { display: flex; align-items: center; gap: 16px; font-size: 11px; font-weight: 500; }
  .main-nav a { color: var(--ink); text-decoration: none; }
  .main-nav .is-current { border: 1px solid var(--sky); padding: 2px 6px; }
  .main-nav .login { background: var(--sky); color: var(--white); padding: 3px 10px; }

  .prices-intro { text-align: center; margin-top: 8px; }
  .prices-title {
    display: inline-block; font-family: "Barlow Condensed", sans-serif; font-weight: 600;
    font-size: 28px; line-height: 32px; color: var(--deep); padding: 0 16px 2px;
    border-bottom: 2px solid var(--deep); letter-spacing: .5px;
  }
  .prices-lead { font-size: 11.5px; font-weight: 500; line-height: 16px; margin: 8px auto 0; width: 640px; }

  .billing-toggle { display: flex; justify-content: center; margin-top: 8px; }
  .billing-toggle span {
    font-family: "Barlow Condensed", sans-serif; font-size: 14px; font-weight: 500; line-height: 16px;
    padding: 4px 16px; background: var(--toggle-off); color: #6e6e6e;
  }
  .billing-toggle .is-active { background: var(--deep); color: var(--white); font-weight: 600; }

  .plans { display: flex; justify-content: center; align-items: flex-start; gap: 14px; margin-top: 8px; }
  .plan {
    width: 280px; margin-top: 20px; background: var(--white);
    box-shadow: 0 2px 8px rgba(0,0,0,.22); border-radius: 3px; overflow: hidden;
  }
  .plan--featured { width: 300px; margin-top: 0; }
  .plan-head { background: var(--sky); color: var(--white); text-align: center; padding-top: 7px; height: 60px; }
  .plan--featured .plan-head { background: var(--deep); height: 70px; padding-top: 10px; }
  .plan-name { font-family: "Barlow Condensed", sans-serif; font-weight: 700; font-size: 26px; line-height: 1; letter-spacing: .5px; }
  .plan-volume { font-family: "Raleway", sans-serif; font-size: 10px; margin-top: 2px; }
  .plan-price {
    position: relative; z-index: 1; width: 76%; margin: -14px auto 0; background: var(--white);
    border-radius: 14px; box-shadow: 0 2px 5px rgba(0,0,0,.18); text-align: center; padding: 3px 0;
    font-family: "Barlow Condensed", sans-serif; font-weight: 600; font-size: 18px; line-height: 20px; color: #333;
  }
  .plan-price small { font-size: 12px; color: var(--sky); font-weight: 500; }
  .plan--featured .plan-price small { color: var(--deep); }
  .plan-features { list-style: none; margin-top: 6px; }
  .plan-features li { height: 15px; line-height: 15px; text-align: center; font-size: 11px; }
  .plan-features li:nth-child(odd) { background: var(--row-alt); }
  .plan-features .is-off { color: var(--muted); }
  .plan-cta { text-align: center; padding: 7px 0 9px; }
  .plan-cta a {
    display: inline-block; background: var(--deep); color: var(--white); text-decoration: none;
    font-size: 11px; font-weight: 500; line-height: 13px; padding: 5px 16px; letter-spacing: .3px;
  }

  .enterprise-band {
    position: absolute; left: 0; right: 0; bottom: 0; height: 96px;
    background: linear-gradient(90deg, var(--band) 0%, #d6e6ed 60%, #b9ccd4 100%);
    border-top-left-radius: 140px 96px;
    display: flex; justify-content: center; gap: 46px; padding: 18px 60px 0 150px; text-align: center;
  }
  .enterprise-item { width: 290px; }
  .enterprise-item h3 { font-size: 13px; font-weight: 500; margin-bottom: 4px; }
  .enterprise-item p { font-size: 10px; line-height: 1.35; }
</style>
</head>
<body>
  <header class="site-header">
    <a class="brand" href="https://paperlynx.example/">
      <span class="brand-mark"></span>
      <span class="brand-name">PAPERLYNX</span>
    </a>
    <nav class="main-nav">
      <a href="#">Home</a>
      <a href="#">Customer Cases</a>
      <a href="#">Video</a>
      <a href="#">Live Demo</a>
      <a href="#" class="is-current">Prices</a>
      <a href="#">About Us</a>
      <a href="#" class="login">Login</a>
      <a href="#">English</a>
    </nav>
  </header>

  <section class="prices-intro">
    <h1 class="prices-title">PRICES</h1>
    <p class="prices-lead">Choose between three different standard models in relation to which contracts you want automated. Contact us if you have more than five contracts, and we will tailor an Enterprise model that is adapted to your needs.</p>
    <div class="billing-toggle"><span>Monthly Payment</span><span class="is-active">Annually Payment</span></div>
  </section>

  <section class="plans">
    <article class="plan">
      <div class="plan-head"><h2 class="plan-name">STARTER</h2><p class="plan-volume">250 documents / Year</p></div>
      <div class="plan-price">DDK 795 <small>Per Month</small></div>
      <ul class="plan-features">
        <li>1 contract templates</li><li>1 user</li><li>+ DKK 95 per additional user</li>
        <li>Export to Text</li><li>Export to Pdf</li><li>Own design</li>
        <li class="is-off">Digital signature</li><li class="is-off">Reviewproces</li><li class="is-off">More languages</li>
        <li class="is-off">Product listing</li><li class="is-off">Employee posting</li><li class="is-off">Documents in mail</li>
        <li class="is-off">Integration to CRM</li><li class="is-off">Customer/client request</li><li class="is-off">Raw data in CSV</li>
        <li class="is-off">API access</li>
      </ul>
      <div class="plan-cta"><a href="#">BOOK DEMO</a></div>
    </article>

    <article class="plan plan--featured">
      <div class="plan-head"><h2 class="plan-name">PRO</h2><p class="plan-volume">1000 documents / Year</p></div>
      <div class="plan-price">DDK 1,595 <small>Per Month</small></div>
      <ul class="plan-features">
        <li>2 contract templates</li><li>1 user</li><li>+ DKK 95 per additional user</li>
        <li>Export to Text</li><li>Export to Pdf</li><li>Own design</li>
        <li>Digital signature</li><li>Reviewproces</li><li>More languages</li>
        <li>Product listing</li><li>Employee posting</li><li>Documents in mail</li>
        <li>Integration to CRM</li><li class="is-off">Customer/client request</li><li class="is-off">Raw data in CSV</li>
        <li class="is-off">API access</li>
      </ul>
      <div class="plan-cta"><a href="#">BOOK DEMO</a></div>
    </article>

    <article class="plan">
      <div class="plan-head"><h2 class="plan-name">BUSINESS</h2><p class="plan-volume">2000 documents / Year</p></div>
      <div class="plan-price">DDK 2795 <small>Per Month</small></div>
      <ul class="plan-features">
        <li>4 contract templates</li><li>1 user</li><li>+ DKK 95 per additional user</li>
        <li>Export to Text</li><li>Export to Pdf</li><li>Own design</li>
        <li>Digital signature</li><li>Reviewproces</li><li>More languages</li>
        <li>Product listing</li><li>Employee posting</li><li>Documents in mail</li>
        <li>Integration to CRM</li><li>Customer/client request</li><li>Raw data in CSV</li>
        <li>API access</li>
      </ul>
      <div class="plan-cta"><a href="#">BOOK DEMO</a></div>
    </article>
  </section>

  <section class="enterprise-band">
    <div class="enterprise-item">
      <h3>Enterprise model</h3>
      <p>We can tailor a model adapted to your business with unlimited use.</p>
    </div>
    <div class="enterprise-item">
      <h3>Number of templates and users</h3>
      <p>If you have many contracts, we tailor a model for you. We can automate as many offers, contracts and other documents as you need, just as we can give access to all the users you want.</p>
    </div>
    <div class="enterprise-item">
      <h3>Continuous update</h3>
      <p>We can also offer continuous updating of your automated documents if you do not want to make the updates yourself.</p>
    </div>
  </section>
</body>
</html>
```